Venture Capital Investment Firm

We are looking to overhaul our existing website (substantially), with only using the same logos (which we can provide).
We are an investment firm that focuses on making loans to late stage technology companies. Our site should ultimately look like other venture capital firms, and look modern and fresh. We have an existing website www.norvellhub.com which this will be replacing, although we will be using a lot of the existing written content, and potentially the numbers of pages we will need, we are not wed to anything else. Please feel free to shoot any questions at any time and thank you in advance for your help!
Websites we like as examples:
https://www.tesmarkfund.com/
https://www.brindlewoodpartners.com/
Target Market(s)
Potential investors who will invest in our firm, as well as potentially companies that are looking to borrow money from us.
Coding
Coded - Design and coding required
Number of Pages Required
5+ page
Colors
Designer to choose colors to be used in the design.
Look and feel

```html
<!DOCTYPE html>
<html lang="en">
<head>
<meta charset="utf-8">
<title>Norvell Hub Investment Partners</title>
<link href="https://fonts.googleapis.com/css2?family=Cinzel:wght@700&family=Montserrat:wght@300;400&display=swap" rel="stylesheet">
<style>
:root{
  --navy:#0b0b3b;
  --ink:#333;
  --muted:#555;
  --soft:#f4f4f5;
  --line:#e1e1e6;
  --royal:#0808a0;
  --field:#1616b4;
  --white:#fff;
}
*{margin:0;padding:0;box-sizing:border-box}
html,body{width:1200px;height:2359px;overflow:hidden;background:var(--white)}
body{font-family:"Montserrat",sans-serif;color:var(--ink);position:relative}
.serif{font-family:"Cinzel",serif;font-weight:700}

.hero{position:absolute;left:0;top:0;width:1200px;height:700px}
.brand{position:absolute;left:78px;top:104px;font-size:118px;line-height:1;color:var(--navy);letter-spacing:2px}
.hero-icon{position:absolute;left:76px;top:322px}
.hero-title{position:absolute;left:79px;top:382px;font-size:48px;line-height:53px;color:var(--navy);letter-spacing:1px}
.hero-sub{position:absolute;left:80px;top:505px;font-size:22px;line-height:34px;letter-spacing:.6px;color:var(--ink);font-weight:400}

.nav-grid{position:absolute;left:769px;top:65px;width:354px;display:grid;grid-template-columns:177px 177px;grid-template-rows:188px 187px 197px;border:1px solid var(--line);background:var(--soft)}
.nav-cell{border-right:1px solid var(--line);border-bottom:1px solid var(--line);display:flex;flex-direction:column;align-items:center;justify-content:center;text-align:center;font-size:15px;line-height:29px;letter-spacing:.3px;color:var(--navy);padding:8px}
.nav-cell:nth-child(2n){border-right:none}
.nav-cell:nth-child(n+5){border-bottom:none}
.nav-cell.active{background:var(--white)}
.nav-cell svg{margin-bottom:10px}

.about-visual{position:absolute;left:77px;top:733px;width:544px;height:542px;background:radial-gradient(circle at 50% 45%,#1d3df0 0%,#0a1bb0 22%,#050a55 50%,#020320 100%)}
.about-copy{position:absolute;left:673px;top:738px;width:456px;font-size:14.4px;line-height:27px;font-weight:300;color:var(--muted)}
.about-copy p+p{margin-top:54px}

.experience{position:absolute;left:0;top:1372px;width:1200px;height:582px;background:var(--soft);text-align:center}
.experience h2{position:absolute;top:72px;width:100%;font-size:40px;color:var(--navy);letter-spacing:1px}
.stats{position:absolute;top:148px;left:0;width:100%}
.stat{position:absolute;width:200px;margin-left:-100px}
.stat strong{display:block;font-family:"Cinzel",serif;font-weight:700;font-size:40px;line-height:50px;color:var(--navy)}
.stat span{display:block;font-size:14.4px;line-height:27px;font-weight:300;color:var(--muted)}
.exp-copy{position:absolute;top:300px;left:110px;width:980px;font-size:14.4px;line-height:27px;font-weight:300;color:var(--muted)}
.exp-copy p+p{margin-top:27px}

.footer{position:absolute;left:0;top:1954px;width:1200px;height:343px;background:var(--royal);color:var(--white)}
.footer-brand{position:absolute;left:96px;top:118px;width:286px;text-align:center}
.footer-brand .name{font-size:34px;letter-spacing:1px;line-height:40px}
.footer-brand a{display:inline-block;margin-top:16px;color:var(--white);font-size:15px;letter-spacing:.5px}
.footer h3{font-size:19px;letter-spacing:.6px;position:absolute;top:34px}
.contact h3{left:436px}
.contact-item{position:absolute;left:433px;display:flex;gap:24px;font-size:14.4px;line-height:27px;font-weight:300;letter-spacing:.5px}
.contact-item svg{flex:none;margin-top:6px}
.newsletter h3{left:793px}
.newsletter p{position:absolute;left:793px;top:72px;width:330px;font-size:14.4px;line-height:27px;font-weight:300}
.field{position:absolute;left:791px;width:322px;height:46px;background:var(--field);border:1px solid #2a2fc4;padding:0 15px;font-size:14px;line-height:44px;font-weight:300;color:#dde}
.subscribe{position:absolute;left:791px;top:251px;width:161px;height:52px;border-radius:26px;background:var(--white);color:var(--navy);font-size:18px;letter-spacing:1px;line-height:52px;text-align:center}

.copyright{position:absolute;left:0;top:2297px;width:1200px;height:62px;background:var(--soft);text-align:center;font-size:14.4px;line-height:62px;color:var(--ink)}
</style>
</head>
<body>

<header class="hero">
  <div class="brand serif">Norvell</div>
  <svg class="hero-icon" width="42" height="54" viewBox="0 0 42 54" fill="none" stroke="#0b0b3b" stroke-width="2">
    <path d="M21 2a16 16 0 0 0-10 28.5c2 1.8 3 4 3 6.5v3h14v-3c0-2.5 1-4.7 3-6.5A16 16 0 0 0 21 2z"/>
    <path d="M21 2v38M14 44h14M15 48h12M2 53h38"/>
  </svg>
  <h1 class="hero-title serif">We Started With A<br>Big Idea</h1>
  <p class="hero-sub">FINANCE PROVEN INNOVATION WITH A<br>DIFFERENT APPROACH</p>

  <nav class="nav-grid">
    <div class="nav-cell active">
      <svg width="40" height="52" viewBox="0 0 40 52" fill="none" stroke="#0b0b3b" stroke-width="2"><path d="M20 2a15 15 0 0 0-9 27c2 1.7 3 4 3 6v3h12v-3c0-2 1-4.3 3-6A15 15 0 0 0 20 2z"/><path d="M20 2v36M14 42h12M15 46h10M3 51h34"/></svg>
      WE STARTED<br>WITH A BIG IDEA</div>
    <div class="nav-cell">
      <svg width="52" height="44" viewBox="0 0 52 44" fill="none" stroke="#0b0b3b" stroke-width="2"><circle cx="18" cy="26" r="9"/><circle cx="18" cy="26" r="3.5"/><circle cx="38" cy="10" r="6"/><circle cx="40" cy="32" r="5"/><path d="M18 13v4M18 35v4M5 26h4M27 26h4M9 17l3 3M24 32l3 3M27 17l-3 3M12 32l-3 3"/></svg>
      WHAT WE LOOK<br>FOR</div>
    <div class="nav-cell">
      <svg width="54" height="40" viewBox="0 0 54 40" fill="none" stroke="#0b0b3b" stroke-width="2"><circle cx="27" cy="12" r="8"/><path d="M13 38c0-8 6-14 14-14s14 6 14 14z"/><circle cx="12" cy="15" r="6"/><circle cx="42" cy="15" r="6"/><path d="M2 34c0-6 4-10 9-10M52 34c0-6-4-10-9-10"/></svg>
      OUR TEAM</div>
    <div class="nav-cell">
      <svg width="40" height="52" viewBox="0 0 40 52" fill="none" stroke="#0b0b3b" stroke-width="2"><circle cx="20" cy="19" r="16"/><circle cx="20" cy="19" r="10"/><path d="M15 19l4 4 7-7M10 32l-4 18 8-5 4 6M30 32l4 18-8-5-4 6"/></svg>
      OUR VALUES</div>
    <div class="nav-cell">
      <svg width="52" height="52" viewBox="0 0 52 52" fill="none" stroke="#0b0b3b" stroke-width="2"><circle cx="30" cy="12" r="10"/><path d="M33 8h-5a2 2 0 0 0 0 4h4a2 2 0 0 1 0 4h-5M30 5v2M30 17v2M30 22v12M2 38l10-4c4-1 8 0 12 2h8a3 3 0 0 1 0 6H20M2 48l10-3 14 3 22-12a3 3 0 0 0-3-5l-13 7"/></svg>
      OUR INVESTMENTS</div>
    <div class="nav-cell">
      <svg width="54" height="46" viewBox="0 0 54 46" fill="none" stroke="#0b0b3b" stroke-width="2"><rect x="8" y="2" width="44" height="42"/><path d="M8 12H2v32h6M16 14h28M16 22h28M16 30h28M16 38h28"/></svg>
      NEWS</div>
  </nav>
</header>

<section class="about">
  <div class="about-visual" role="img" aria-label="Glowing blue light bulb with a brain inside, set against a dark navy background"></div>
  <div class="about-copy">
    <p>Norvell Hub is a private investment firm unique in its dual focus on life science and technology credit opportunities.&nbsp; Our ambidextrous approach to investing reflects a broad recognition and appreciation for the critical role intellectual property plays in the successful commercialization of products.&nbsp; We apply our extensive industry expertise to assess the revenue visibility created by these assets and offer a range of creative financing solutions.</p>
    <p>A pioneer in providing life science structured credit beginning in 2004, the Norvell Hub team was the first to introduce flexible structured credit to the technology sector in 2014.&nbsp; Our team was also early to recognize the potential of "non-core" assets beyond drug royalties, acquiring over $300M of branded generics offering predictable cash flows from large pharmaceutical firms and partnering with entrepreneurial teams to successfully manage these brands.</p>
  </div>
</section>

<section class="experience">
  <h2 class="serif">OUR EXPERIENCE</h2>
  <div class="stats">
    <div class="stat" style="left:388px"><strong>$1.2B</strong><span>Over $1.2B invested<br>by our partners</span></div>
    <div class="stat" style="left:576px"><strong>40+</strong><span>40 Life science and<br>technology investments</span></div>
    <div class="stat" style="left:794px"><strong>12+</strong><span>Over a decade innovating<br>financing structures</span></div>
  </div>
  <div class="exp-copy">
    <p>We bring over 40 years of collective experience to our investments, including over $1.2B invested within structured credit, milestones and royalties, and the acquisition of legacy assets from some of the world's largest and most well respected pharmaceutical companies.&nbsp; In addition, members of the Norvell Hub team have played senior roles in executing over $75B of M&amp;A, equity, and debt financings in the life science and technology sectors.</p>
    <p>Along the way we've built strong relationships and friendships with entrepreneurial management teams, investors, and executives who acquire and commercialize innovative products and technologies.&nbsp; These relationships offer Norvell Hub unique insight into the industries, companies, and products where we invest.</p>
  </div>
</section>

<footer class="footer">
  <div class="footer-brand">
    <div class="name serif">Norvell Hub</div>
    <a href="#">Legal Disclaimer</a>
  </div>
  <div class="contact">
    <h3 class="serif">CONTACT US</h3>
    <div class="contact-item" style="top:78px">
      <svg width="18" height="26" viewBox="0 0 18 26" fill="#fff"><path d="M9 0a9 9 0 0 0-9 9c0 7 9 17 9 17s9-10 9-17a9 9 0 0 0-9-9zm0 12.5A3.5 3.5 0 1 1 9 5.5a3.5 3.5 0 0 1 0 7z"/></svg>
      <div>SAN FRANCISCO<br>418 Larkmoor Street #210<br>San Francisco, CA&nbsp; 94107</div>
    </div>
    <div class="contact-item" style="top:180px">
      <svg width="22" height="16" viewBox="0 0 22 16" fill="#fff"><path d="M0 0h22v2L11 9 0 2zM0 4l11 7 11-7v12H0z"/></svg>
      <div>GENERAL INQUIRIES : :<br>inquiries@norvellhub.com</div>
    </div>
    <div class="contact-item" style="top:248px">
      <svg width="22" height="16" viewBox="0 0 22 16" fill="#fff"><path d="M0 0h22v2L11 9 0 2zM0 4l11 7 11-7v12H0z"/></svg>
      <div>MEDIA INQUIRIES :<br>media@norvellhub.com</div>
    </div>
  </div>
  <div class="newsletter">
    <h3 class="serif">NEWSLETTER</h3>
    <p>Would you like to receive our exclusive news and update for signup our newsletter !</p>
    <div class="field" style="top:139px">Enter Name *</div>
    <div class="field" style="top:194px">Enter Email *</div>
    <div class="subscribe serif">SUBSCRIBE</div>
  </div>
</footer>

<div class="copyright">©2019 Norvell Hub Investment Partners LLC.&nbsp; All Rights Reserved.</div>

</body>
</html>
```